Harbor Crestline (Business Card Design)

Need business cards designed. Something modern, chic, and sleek. Mabye the back of the card should be the navy blue that is in the logo and then just the logo on the back.

Target Market(s)

Those in the hotel, office, and renovation industry

Contact Information for Business Card

1. Logo 2. Dorian Fenwick 3. CEO/Founder 4. Phone: (833) HarbCre / (833) 427-2731 5. Email: dorian@theharborcrestline.com 6. Website: www.theharborcrestline.com

Font styles to use
Other font styles liked:
• Look at the logo font and base the font for everything else off of that.

Colors
0054AA
0677BA
7BADD7
CADEEF
E8F1F8

Requirements
Must have
• Colors that are associated in the logo
Nice to have
• Sleek modern clean and chic design.

```html
<!DOCTYPE html>
<html lang="en">
<head>
<meta charset="utf-8">
<title>Harbor Crestline – Business Card</title>
<link rel="stylesheet" href="https://fonts.googleapis.com/css2?family=Montserrat:wght@500;600&family=Open+Sans:wght@400;700&display=swap">
<style>
  :root {
    --scene: #232323;
    --navy: #0e1940;
    --navy-deep: #0b1436;
    --pattern: #1a2a63;
    --gold: #d1a743;
    --white: #ffffff;
    --shadow: rgba(0, 0, 0, 0.55);
  }
  * { box-sizing: border-box; margin: 0; padding: 0; }
  html, body { width: 1200px; height: 780px; overflow: hidden; }
  body { background: var(--scene); position: relative; font-family: "Open Sans", sans-serif; }

  .card {
    position: absolute;
    width: 540px;
    height: 309px;
    border-radius: 4px;
    background: var(--navy);
    box-shadow: 0 14px 30px var(--shadow);
    overflow: hidden;
  }
  .card--back { left: 70px; top: 70px; }
  .card--front { left: 590px; top: 400px; }

  /* Back */
  .back-pattern {
    position: absolute;
    inset: 0;
    background: linear-gradient(135deg, var(--navy-deep) 0%, var(--pattern) 100%);
  }
  .back-brand {
    position: absolute;
    right: 26px;
    bottom: 24px;
    display: flex;
    align-items: center;
    gap: 6px;
    font-family: "Montserrat", sans-serif;
    font-weight: 500;
    font-size: 9px;
    letter-spacing: 1px;
    color: var(--white);
    text-transform: uppercase;
    white-space: nowrap;
  }
  .brand-square { width: 10px; height: 10px; background: var(--white); flex: none; }

  /* Front */
  .front-brand {
    position: absolute;
    left: 34px;
    top: 104px;
    display: flex;
    align-items: center;
    gap: 10px;
    font-family: "Montserrat", sans-serif;
    font-weight: 600;
    font-size: 18px;
    letter-spacing: 2px;
    color: var(--white);
    text-transform: uppercase;
    white-space: nowrap;
  }
  .front-brand .brand-square { width: 14px; height: 14px; background: var(--gold); }

  .holder {
    position: absolute;
    right: 48px;
    top: 36px;
    text-align: right;
    white-space: nowrap;
  }
  .holder-name {
    font-weight: 700;
    font-size: 26px;
    line-height: 1;
    color: var(--white);
  }
  .holder-name .first { color: var(--gold); }
  .holder-role {
    margin-top: 6px;
    font-size: 13px;
    line-height: 1.2;
    color: var(--white);
  }
  .gold-tab {
    position: absolute;
    right: 0;
    top: 32px;
    width: 20px;
    height: 42px;
    background: var(--gold);
  }
  .divider {
    position: absolute;
    left: 34px;
    right: 48px;
    top: 146px;
    height: 1px;
    background: var(--white);
  }

  .contact {
    position: absolute;
    left: 34px;
    top: 164px;
    color: var(--white);
    font-size: 12.5px;
    line-height: 1.35;
    white-space: nowrap;
  }
  .address { margin-bottom: 12px; }
  .contact-list { list-style: none; }
  .contact-list li { display: flex; align-items: center; gap: 8px; }
  .contact-list svg { width: 12px; height: 12px; flex: none; }
</style>
</head>
<body>

<section class="card card--back" aria-label="Card back">
  <div class="back-pattern" role="img" aria-label="Repeating brand pattern on navy"></div>
  <div class="back-brand"><span class="brand-square"></span>Harbor Crestline</div>
</section>

<section class="card card--front" aria-label="Card front">
  <div class="gold-tab"></div>
  <div class="holder">
    <p class="holder-name"><span class="first">Dorian</span> Fenwick</p>
    <p class="holder-role">CEO/Founder</p>
  </div>

  <div class="front-brand"><span class="brand-square"></span>Harbor Crestline</div>
  <div class="divider"></div>

  <div class="contact">
    <p class="address">4120 Wexley Park Dr<br>Suite 210, Alderton, MD 21090</p>
    <ul class="contact-list">
      <li>
        <svg viewBox="0 0 24 24" aria-hidden="true"><path fill="var(--gold)" d="M6.6 10.8a15.1 15.1 0 0 0 6.6 6.6l2.2-2.2a1 1 0 0 1 1-.25 11.4 11.4 0 0 0 3.6.57 1 1 0 0 1 1 1V20a1 1 0 0 1-1 1A17 17 0 0 1 3 4a1 1 0 0 1 1-1h3.5a1 1 0 0 1 1 1c0 1.25.2 2.45.57 3.6a1 1 0 0 1-.25 1z"/></svg>
        (833) HarbCre / (833) 427-2731
      </li>
      <li>
        <svg viewBox="0 0 24 24" aria-hidden="true"><circle cx="12" cy="12" r="9" fill="none" stroke="var(--gold)" stroke-width="2.4"/><path d="M3 12h18M12 3c3 3 3 15 0 18M12 3c-3 3-3 15 0 18" fill="none" stroke="var(--gold)" stroke-width="1.8"/></svg>
        www.theharborcrestline.com
      </li>
      <li>
        <svg viewBox="0 0 24 24" aria-hidden="true"><rect x="2" y="5" width="20" height="14" rx="1.5" fill="var(--gold)"/><path d="M2.5 6l9.5 7 9.5-7" fill="none" stroke="var(--navy)" stroke-width="1.8"/></svg>
        dorian@theharborcrestline.com
      </li>
    </ul>
  </div>
</section>

</body>
</html>
```